Snoutsaver.net Dog Coupon Site Website Design

TailThrift - Dog Coupon Site Design Brief

Project Overview
**Site Name:** SnoutSaver.net
**Purpose:** A modern coupon aggregation platform specifically for dog and pet-related products and services
**Target Audience:** Dog owners, pet enthusiasts, budget-conscious pet parents

Brand Identity & Visual Direction

Typography
- **Headers:** Modern sans-serif (Inter or similar) - Clean and friendly
- **Body:** Readable sans-serif with good mobile legibility
- **Accent:** Playful but professional font for coupon codes

Design Principles
- **Flat Design:** Clean, minimal with subtle shadows
- **Friendly & Approachable:** Rounded corners, soft edges
- **Trust-Building:** Clear pricing, transparent savings
- **Scannable:** Easy-to-read coupon codes and offers

## User Experience & Functionality

### Homepage Features
1. **Hero Section**
- Clear value proposition
- Search functionality
- Featured savings highlight

2. **Coupon Cards**
- One-click copy functionality
- Clear discount display
- Store/brand logos
- Expiration dates
- "Get Deal" call-to-action

3. **Navigation**
- Categories (Food, Toys, Health, Services, etc.)
- Popular stores
- Latest deals

### Interactive Elements
- **Copy Button:** Instant feedback when coupon copied
- **Deal Pages:** Detailed offer information, terms, store details
- **Search & Filter:** By category, store, discount amount
- **Mobile Menu:** Hamburger navigation for mobile

## Technical Requirements

### Responsive Design
- **Mobile-First:** Optimized for touch interactions
- **Tablet:** Adapted layout for medium screens
- **Desktop:** Full-width utilization with sidebar potential

### Performance
- **Fast Loading:** Optimized images, minimal JavaScript
- **Accessibility:** WCAG compliant, screen reader friendly
- **SEO Optimized:** Structured data for deals and offers

## Content Strategy

### Deal Categories
- Dog Food & Treats
- Toys & Accessories
- Health & Grooming
- Training & Services
- Outdoor & Travel

### Key Messaging
- "Save on everything your dog loves"
- "Verified deals updated daily"
- "Your pup deserves the best for less"

## Conversion Optimization

### Trust Elements
- Deal verification badges
- User reviews/ratings
- Clear savings calculations
- Expiration date transparency

### Call-to-Actions
- "Copy Code" (primary action)
- "Get Deal" (secondary action)
- "View All [Store] Deals"

## Success Metrics
- Coupon copy rate
- Click-through to retailer
- User return visits
- Mobile vs desktop usage
- Category performance

This design brief ensures a user-friendly, trustworthy platform that makes finding and using pet deals effortless while maintaining a warm, dog-loving community feel.

1. Design Objective
Create a warm, energetic space where dog lovers instantly feel welcomed and confident they’re finding genuine savings for their furry friends. Everything from the layout to the smallest icon should reinforce trust, delight, and simplicity.
2. Visual Personality
Color Palette: Soft, cheerful hues—think warm yellows and gentle blues—that evoke sunshine and playfulness without overwhelming.
Typography:
Headings: A modern, friendly sans‑serif (like Inter) with open letterforms to feel approachable.
Body Copy: Highly legible sans‑serif with generous line spacing for comfort on small screens.
Accent Font: A slightly quirky, hand‑drawn style used sparingly for coupon codes and special call‑outs, giving a personal, “paw‑picked” touch.
Imagery & Icons: Real‑life photographs of happy dogs interspersed with clean line‑icons of bones, paw prints, and hearts. Rounded shapes and subtle shadows keep the look soft and contemporary.
3. Layout & Hierarchy
Hero Area:
Full‑bleed image of a joyful dog, overlaid with a single, punchy tagline (“Save on everything your dog loves”).
Prominent search bar centered to invite exploration.
Offer Grid:
Generous white space around each coupon card so the eye can rest and scan easily.
Coupon cards feature a bold discount label, brand logo, and a friendly “Get Deal” button.
A playful “Copied!” animation briefly replaces the button once the code is grabbed.
Navigation:
A fixed header with clear category labels (Food, Toys, Health, Services).
A secondary “Popular Stores” carousel below to spotlight key partners.
4. Interaction & Motion
Micro‑interactions:
Hover state for cards subtly lifts the card and deepens its shadow, inviting a click.
Copy‑code button pulses once on hover, hinting at its one‑click magic.
Transitions:
Smooth fades between deal filters and search results to reassure users that the site is responding.
Loading indicators shaped like spinning collars or wagging tails to keep the theme consistent.
5. Accessibility & Inclusivity
Ensure all text meets contrast standards so every pet parent—regardless of vision—can read offers with ease.
Interactive elements sized for easy tapping on touchscreens.
Alt‑text for all imagery describing dogs, products, and actions for screen‑reader users.
6. Emotional Tone
From the moment someone lands on SnoutSaver.net, they should feel the joy of treating their dog without guilt. Friendly copy (“Your pup deserves the best for less”) paired with bright visuals will create a sense of community and shared passion.
7. Success by Design
Scan‑ability: Users should spot great deals in under two seconds.
Trust Signals: Badges (“Verified Savings”), clear expiration dates, and reviewer star icons should feel earned and prominent.
Return Visits: A “My Favorite Deals” heart icon encourages saving and returning, reinforced by subtle reminders in the UI.
This design approach keeps dog lovers front and center—making sure every graphic, font choice, and interaction feels like it was lovingly tailored for them.

Target Market(s)

Dog Lovers looking for good deals

Industry/Entity Type

Coupon Code

Number of Pages Required

4 page

Font styles to use
Sans Serif

Requirements
Must have
• Modern look, coupon copy cards it's a deal site and I want the coupon code and copy in the coupon card, blog section, review section, modern footer/header
Nice to have
• Modern coupon code website, easy to use

```html
<!DOCTYPE html>
<html lang="en">
<head>
<meta charset="utf-8">
<title>SnoutSaver – Dog Coupons &amp; Deals</title>
<link href="https://fonts.googleapis.com/css2?family=Poppins:wght@500;600;700;800&family=Inter:wght@400;500;600;700&family=Great+Vibes&display=swap" rel="stylesheet">
<style>
:root{
  --navy:#0f1b5c;
  --orange:#f15a29;
  --orange-soft:#f7ebe4;
  --sky:#e2f3fb;
  --sky-pill:#d4ecf9;
  --peach:#f7efea;
  --lilac:#efeef9;
  --grey-bar:#d6d6d6;
  --line:#e1e1e1;
  --text:#1c1c1c;
  --muted:#7a7a7a;
  --white:#ffffff;
  --yellow:#f6c343;
}
*{box-sizing:border-box;margin:0;padding:0}
html,body{width:1200px;height:4967px;overflow:hidden}
body{font-family:'Inter',sans-serif;color:var(--text);background:var(--white);position:relative}
.abs{position:absolute}
.heading{font-family:'Poppins',sans-serif;font-weight:700;color:var(--navy);font-size:38px;line-height:1.2}
.center{left:0;width:1200px;text-align:center}
.btn{display:flex;align-items:center;justify-content:center;gap:6px;background:var(--orange);color:var(--white);font-weight:700;font-size:15px;border-radius:30px;font-family:'Poppins',sans-serif}
.arrow{width:24px;height:24px;border-radius:50%;display:flex;align-items:center;justify-content:center}
.arrow.prev{background:#7b7b7b}
.arrow.next{background:var(--orange)}

/* top bar */
.topbar{top:0;left:0;width:1200px;height:38px;background:var(--navy);display:flex;align-items:center;justify-content:center;gap:10px;color:var(--white);font-size:12px}
.topbar .pill{background:var(--sky-pill);color:var(--navy);font-weight:700;padding:3px 14px;border-radius:12px}
/* header */
.brand{display:flex;align-items:center;gap:8px;font-family:'Poppins',sans-serif;font-weight:700;font-size:26px;color:var(--navy)}
.brand .dot{width:22px;height:22px;border-radius:50%;background:var(--navy)}
.search{left:351px;top:58px;width:497px;height:42px;border:1px solid #c9c9c9;border-radius:21px;background:#f3f3f3;display:flex;align-items:center;padding-left:26px;font-size:15px;color:#555;overflow:hidden}
.search .go{position:absolute;right:0;top:0;width:56px;height:40px;background:var(--orange);display:flex;align-items:center;justify-content:center;border-radius:0 21px 21px 0}
.nav{top:120px;left:0;width:1200px;height:38px;background:var(--grey-bar);font-size:13px;font-weight:700;color:var(--navy)}
.nav span{position:absolute;top:11px}
/* hero */
.hero{top:158px;left:0;width:1200px;height:459px;border-radius:0 0 70px 70px;overflow:hidden;background:linear-gradient(100deg,#3a3c2a 0%,#4d5237 35%,#7a5a3a 60%,#a0603a 75%,#6d6a5a 100%)}
.hero .script{left:110px;top:52px;font-family:'Great Vibes',cursive;font-size:72px;color:var(--white);line-height:1}
.hero h1{left:110px;top:132px;font-family:'Poppins',sans-serif;font-weight:700;color:var(--white);font-size:46px;line-height:1.2}
.hero h1 b{font-size:54px}
.hero p{left:116px;top:264px;color:var(--white);font-size:16px}
.hero .btn{left:106px;top:310px;width:138px;height:44px}
/* popular deal */
.deal{top:779px;width:484px;height:287px;border-radius:10px;overflow:hidden;display:flex;box-shadow:0 2px 8px rgba(0,0,0,.08)}
.deal .info{width:240px;background:var(--navy);color:var(--white);padding:78px 0 0 33px;position:relative}
.deal .info h3{font-family:'Poppins',sans-serif;font-size:20px;font-weight:700}
.deal .info .sub{font-size:15px;margin-top:4px}
.code{position:absolute;left:33px;top:155px;display:flex}
.code .box{width:108px;height:50px;background:var(--orange);display:flex;flex-direction:column;align-items:center;justify-content:center;font-family:'Poppins',sans-serif;font-weight:700;font-size:19px;line-height:1}
.code .box small{font-size:10px;font-weight:500;margin-top:3px}
.code .tag{width:20px;height:50px;background:var(--yellow);color:var(--navy);font-size:9px;font-weight:700;writing-mode:vertical-rl;display:flex;align-items:center;justify-content:center}
.deal .get{position:absolute;left:33px;top:236px;font-weight:700;font-size:15px}
.deal .photo{flex:1;position:relative}
.deal .photo .badge{position:absolute;right:14px;top:14px;width:74px;height:32px;border-radius:6px;background:var(--white)}
/* steps */
.step{top:1257px;width:307px;height:131px;border:1px solid var(--line);border-radius:8px;background:var(--white)}
.step .num{position:absolute;right:24px;top:-12px;width:24px;height:24px;border-radius:50%;background:var(--sky-pill);color:var(--navy);font-size:12px;font-weight:700;display:flex;align-items:center;justify-content:center}
.step .ico{position:absolute;left:18px;top:38px;width:56px;height:56px;border-radius:50%;background:#f1f4fa;display:flex;align-items:center;justify-content:center}
.step h4{position:absolute;left:96px;top:34px;font-size:17px;font-weight:700;color:var(--navy)}
.step p{position:absolute;left:96px;top:60px;width:190px;font-size:13px;color:var(--muted);line-height:1.5}
/* coupon section */
.coupons{top:1469px;left:0;width:1200px;height:559px;background:var(--sky);border-radius:0 0 70px 70px}
.ccard{top:1612px;width:220px;height:345px;background:var(--white);border-radius:8px;overflow:hidden;box-shadow:0 2px 8px rgba(0,0,0,.07)}
.ccard .photo{height:138px}
.ccard .logo{position:absolute;left:14px;top:118px;width:40px;height:40px;border-radius:50%;background:var(--white);box-shadow:0 1px 4px rgba(0,0,0,.15);display:flex;align-items:center;justify-content:center}
.ccard .logo i{width:18px;height:18px;border-radius:50%;background:#3aa55a}
.ccard .off{position:absolute;left:16px;top:176px;font-size:14px;font-weight:700;color:#333}
.usecode{position:absolute;left:16px;top:202px;background:var(--sky-pill);color:var(--navy);font-size:13px;padding:4px 10px;border-radius:14px;display:flex;align-items:center;gap:5px}
.ccard h5{position:absolute;left:16px;top:252px;font-family:'Poppins',sans-serif;font-size:20px;font-weight:600;color:var(--navy)}
.ccard .btn{position:absolute;left:14px;top:290px;width:122px;height:40px}
/* trending */
.sidebar{left:106px;top:2200px;width:224px;height:401px;border:1px solid var(--line);background:var(--white)}
.cat{position:absolute;left:0;width:222px;height:73px;display:flex;align-items:center;gap:14px;padding-left:16px;font-size:15px;font-weight:700;color:var(--navy);line-height:1.3}
.cat.active{background:var(--orange-soft);color:var(--orange)}
.cat .ci{width:48px;height:48px;border-radius:50%;background:var(--white);border:1px solid #e8e8e8;flex:none;display:flex;align-items:center;justify-content:center}
.offers{left:330px;top:2200px;width:759px;height:73px;background:var(--peach);border:1px solid var(--line);display:flex;align-items:center;justify-content:space-between;padding:0 30px 0 44px}
.offers b{font-size:16px;color:var(--navy)}
.offers span{color:var(--orange);font-weight:700;font-size:15px}
.tcard{top:2329px;width:220px;height:268px;border:1px solid var(--line);background:var(--white);border-radius:4px}
.tlogo{position:absolute;left:22px;top:28px;display:flex;align-items:center;gap:6px;font-weight:700;font-size:13px;color:var(--navy)}
.tlogo i{width:12px;height:12px;border-radius:50%;background:var(--orange)}
.tcard h5{position:absolute;left:22px;top:88px;width:180px;font-family:'Poppins',sans-serif;font-size:19px;font-weight:600;color:var(--navy);line-height:1.25}
.tcard .off{position:absolute;left:22px;top:158px;font-size:15px;font-weight:700;color:var(--orange);display:flex;align-items:center;gap:6px}
.tcard .btn{position:absolute;left:22px;top:192px;width:176px;height:42px}
/* stores */
.stores{top:2695px;left:0;width:1200px;height:693px;background:var(--peach);border-radius:70px 70px 0 0}
.scard{background:var(--white);border:1px solid var(--line)}
.big{left:106px;top:2871px;width:347px;height:374px}
.big .inner{position:absolute;left:15px;top:14px;width:316px;height:200px;border:1px solid var(--line);display:flex;align-items:center;justify-content:center;font-family:'Poppins',sans-serif;font-weight:700;font-size:30px;color:var(--navy)}
.big .pin{position:absolute;right:24px;top:28px;width:26px;height:26px;border-radius:50%;background:var(--orange)}
.big h5{position:absolute;left:0;width:100%;text-align:center;top:238px;font-family:'Poppins',sans-serif;font-size:22px;font-weight:600;color:var(--navy)}
.big .off{position:absolute;left:0;width:100%;top:282px;justify-content:center;font-size:18px}
.off-row{display:flex;align-items:center;gap:7px;color:var(--orange);font-weight:700}
.small{width:185px;height:171px}
.small .name{position:absolute;left:0;width:100%;top:48px;text-align:center;font-family:'Poppins',sans-serif;font-weight:700;font-size:20px;color:var(--navy)}
.small .off{position:absolute;left:0;width:100%;top:120px;justify-content:center;font-size:17px}
/* testimonials */
.tst{top:3580px;width:321px;height:214px;background:var(--lilac);border-radius:6px;padding:34px 28px 0}
.stars{color:var(--orange);font-size:14px;letter-spacing:4px}
.tst p{font-size:12px;color:#333;line-height:1.75;margin-top:10px}
.tst .who{font-size:11px;color:#444;margin-top:10px}
/* newsletter */
.news{left:106px;top:4049px;width:985px;height:343px;background:var(--orange);border-radius:10px}
.news-photo{left:125px;top:3875px;width:386px;height:517px;border-radius:190px 190px 0 0;background:linear-gradient(180deg,#e9d9cb 0%,#c9a78b 55%,#b07a55 100%)}
.news h2{position:absolute;left:479px;top:62px;font-family:'Poppins',sans-serif;font-weight:700;font-size:40px;line-height:1.2;color:var(--white)}
.news p{position:absolute;left:484px;top:166px;width:320px;font-size:15px;color:var(--white);line-height:1.4}
.mail{position:absolute;left:479px;top:218px;width:443px;height:52px;background:var(--white);border-radius:26px;display:flex;align-items:center;padding-left:22px;font-size:13px;color:#666}
.mail .sub{position:absolute;right:4px;top:4px;width:184px;height:44px;background:var(--navy);color:var(--white);border-radius:22px;display:flex;align-items:center;justify-content:center;font-weight:700;font-size:15px}
/* perks */
.perk{top:4452px;display:flex;align-items:center;gap:12px}
.perk b{display:block;font-size:13px;color:var(--navy)}
.perk small{display:block;font-size:10px;color:#555;margin-top:2px;line-height:1.3}
/* footer */
.footer{top:4556px;left:0;width:1200px;height:411px;background:#f6ede6;border-radius:70px 70px 0 0}
.fcol{top:64px}
.fcol h6{font-size:16px;font-weight:700;color:var(--navy);padding-bottom:6px;border-bottom:2px solid var(--orange);display:inline-block}
.fcol a{display:block;font-size:13px;color:#555;text-decoration:none;margin-top:22px}
.vline{top:60px;width:1px;height:300px;background:#d8cfc8}
.social{display:flex;gap:10px}
.social i{width:30px;height:30px;border-radius:50%;border:1px solid #999;background:var(--white)}
.copy{left:0;top:374px;width:1200px;height:37px;background:#ece2da;display:flex;align-items:center;justify-content:center;font-size:13px;color:#333}
</style>
</head>
<body>

<div class="abs topbar"><span class="pill">10% Off</span><span>Welcome to SnoutSaver - &nbsp;Trusted Coupons, Offers</span></div>

<header>
  <div class="abs brand" style="left:66px;top:64px"><span class="dot"></span>SnoutSaver</div>
  <div class="abs search">Search
    <span class="go"><svg width="20" height="20" viewBox="0 0 24 24" fill="none" stroke="#fff" stroke-width="2.5"><circle cx="11" cy="11" r="7"/><path d="M16 16l5 5"/></svg></span>
  </div>
  <svg class="abs" style="left:942px;top:66px" width="28" height="28" viewBox="0 0 24 24" fill="none" stroke="#0f1b5c" stroke-width="1.6"><path d="M6 3h12l4 6-10 12L2 9z"/><path d="M2 9h20M9 3l3 18 3-18"/></svg>
  <svg class="abs" style="left:1004px;top:68px" width="28" height="26" viewBox="0 0 24 22" fill="none" stroke="#0f1b5c" stroke-width="1.8"><path d="M12 20S2 14 2 7.5A4.5 4.5 0 0 1 12 5a4.5 4.5 0 0 1 10 2.5C22 14 12 20 12 20z"/></svg>
  <svg class="abs" style="left:1062px;top:66px" width="28" height="28" viewBox="0 0 24 24" fill="none" stroke="#0f1b5c" stroke-width="1.8"><circle cx="12" cy="8" r="4.5"/><path d="M3 22c0-5 4-8 9-8s9 3 9 8"/></svg>
</header>

<nav class="abs nav"><span style="left:356px">CATEGORIES ⌄</span><span style="left:520px">POPULAR STORES</span><span style="left:726px">LATEST DEALS</span></nav>

<section class="abs hero" role="img" aria-label="Photo of a dachshund lying on a rug chewing a blue rubber toy">
  <div class="abs script">Save On</div>
  <h1 class="abs">Everything<br>Your <b>Dog</b> Loves</h1>
  <p class="abs">Your pup deserves the best for less</p>
  <a class="abs btn">Get Deal →</a>
</section>

<h2 class="abs heading center" style="top:686px">Popular Deal</h2>
<div class="abs arrow prev" style="left:60px;top:903px"><svg width="10" height="10" viewBox="0 0 10 10"><path d="M7 1L3 5l4 4" stroke="#fff" stroke-width="2" fill="none"/></svg></div>
<div class="abs arrow next" style="left:1117px;top:903px"><svg width="10" height="10" viewBox="0 0 10 10"><path d="M3 1l4 4-4 4" stroke="#fff" stroke-width="2" fill="none"/></svg></div>
<article class="abs deal" style="left:106px">
  <div class="info"><h3>Upto 50-80% Off</h3><div class="sub">On Latest Food</div>
    <div class="code"><div class="box">CD499<small>USE CODE</small></div><div class="tag">5% OFF</div></div>
    <div class="get">Get Deal →</div></div>
  <div class="photo" role="img" aria-label="Bag of premium lamb and rice dog food beside a bowl of kibble" style="background:linear-gradient(160deg,#f2f2f2,#dcdcdc 60%,#c9a47e)"><span class="badge"></span></div>
</article>
<article class="abs deal" style="left:611px">
  <div class="info"><h3>Upto 50-80% Off</h3><div class="sub">On Latest Food</div>
    <div class="code"><div class="box">CD499<small>USE CODE</small></div><div class="tag">5% OFF</div></div>
    <div class="get">Get Deal →</div></div>
  <div class="photo" role="img" aria-label="Pink pet food pouch on a blue background" style="background:linear-gradient(160deg,#3a8fc9,#2b6fa8 55%,#e16a93)"><span class="badge"></span></div>
</article>

<h2 class="abs heading" style="left:106px;top:1164px">Three Steps To Save With SnoutSaver</h2>
<div class="abs step" style="left:106px"><span class="num">1</span><span class="ico"><svg width="30" height="30" viewBox="0 0 24 24" fill="none" stroke="#0f1b5c" stroke-width="1.5"><circle cx="10" cy="8" r="4"/><path d="M2 21c0-4 4-7 8-7"/><circle cx="17" cy="17" r="4"/><path d="M15.5 17l1.2 1.2 2-2.2"/></svg></span><h4>Log In</h4><p>Sign up free and start saving today</p></div>
<div class="abs step" style="left:445px"><span class="num">2</span><span class="ico"><svg width="32" height="24" viewBox="0 0 32 24" fill="none" stroke="#0f1b5c" stroke-width="1.5"><path d="M2 4h28v5a3 3 0 0 0 0 6v5H2v-5a3 3 0 0 0 0-6z"/><path d="M12 16l8-8" stroke="#f15a29"/><circle cx="12" cy="9" r="1.3"/><circle cx="20" cy="15" r="1.3"/></svg></span><h4>Use Code</h4><p>Copy the code and apply it at checkout</p></div>
<div class="abs step" style="left:785px"><span class="num">3</span><span class="ico"><svg width="30" height="30" viewBox="0 0 24 24" fill="none" stroke="#0f1b5c" stroke-width="1.5"><path d="M2 17h4l4 2h6l5-4-2-1-4 2h-4"/><path d="M6 17v-3h5l3 2"/><circle cx="15" cy="7" r="3" stroke="#f15a29"/></svg></span><h4>Get Reward</h4><p>Enjoy cashback and savings instantly</p></div>

<section class="abs coupons"></section>
<h2 class="abs heading center" style="top:1528px">Coupon Cards</h2>
<div class="abs arrow prev" style="left:60px;top:1775px"><svg width="10" height="10" viewBox="0 0 10 10"><path d="M7 1L3 5l4 4" stroke="#fff" stroke-width="2" fill="none"/></svg></div>
<div class="abs arrow next" style="left:1117px;top:1775px"><svg width="10" height="10" viewBox="0 0 10 10"><path d="M3 1l4 4-4 4" stroke="#fff" stroke-width="2" fill="none"/></svg></div>

<article class="abs ccard" style="left:106px"><div class="photo" role="img" aria-label="Bulldog puppy playing with toys" style="background:linear-gradient(150deg,#c58a5b,#e9d6c2)"></div><span class="logo"><i></i></span><span class="off">Upto 50-80% Off</span><span class="usecode">🏷 Use Code</span><h5>Lorem Ipsum</h5><a class="btn">Get Deal →</a></article>
<article class="abs ccard" style="left:361px"><div class="photo" role="img" aria-label="Dog with a ball on a yellow background" style="background:linear-gradient(150deg,#f4b63a,#e59a2a)"></div><span class="logo"><i></i></span><span class="off">Upto 50-80% Off</span><span class="usecode">🏷 Use Code</span><h5>Lorem Ipsum</h5><a class="btn">Get Deal →</a></article>
<article class="abs ccard" style="left:615px"><div class="photo" role="img" aria-label="Dog being groomed on a blue background" style="background:linear-gradient(150deg,#3f8fd6,#2c6cb8)"></div><span class="logo"><i></i></span><span class="off">Upto 50-80% Off</span><span class="usecode">🏷 Use Code</span><h5>Lorem Ipsum</h5><a class="btn">Get Deal →</a></article>
<article class="abs ccard" style="left:870px"><div class="photo" role="img" aria-label="Bag of dog treats with biscuits" style="background:linear-gradient(150deg,#4d9de0,#d9b66f)"></div><span class="logo"><i></i></span><span class="off">Upto 50-80% Off</span><span class="usecode">🏷 Use Code</span><h5>Lorem Ipsum</h5><a class="btn">Get Deal →</a></article>

<h2 class="abs heading" style="left:102px;top:2100px">Trending Categories</h2>
<aside class="abs sidebar">
  <div class="cat active" style="top:0"><span class="ci">🥫</span>Dog Food &amp;<br>Treats</div>
  <div class="cat" style="top:97px"><span class="ci">🦴</span>Toys &amp;<br>Accessories</div>
  <div class="cat" style="top:203px"><span class="ci">🧴</span>Health &amp;<br>Grooming</div>
  <div class="cat" style="top:310px"><span class="ci">🐾</span>Training &amp;<br>Services</div>
</aside>
<div class="abs offers"><b>Offers</b><span>Show More →</span></div>
<article class="abs tcard" style="left:353px"><span class="tlogo"><i></i>Reelhaven</span><h5>Lorem Ipsum is simply dummy</h5><span class="off">🏷 Upto 50-80% Off</span><a class="btn">Get Deal →</a></article>
<article class="abs tcard" style="left:611px"><span class="tlogo"><i></i>Reelhaven</span><h5>Lorem Ipsum is simply dummy</h5><span class="off">🏷 Upto 50-80% Off</span><a class="btn">Get Deal →</a></article>
<article class="abs tcard" style="left:870px"><span class="tlogo"><i></i>Reelhaven</span><h5>Lorem Ipsum is simply dummy</h5><span class="off">🏷 Upto 50-80% Off</span><a class="btn">Get Deal →</a></article>

<section class="abs stores"></section>
<h2 class="abs heading center" style="top:2766px">Top Stores</h2>
<article class="abs scard big"><div class="inner">Prismwell</div><span class="pin"></span><h5>Lorem Ipsum</h5><span class="off off-row">🏷 Upto 50-80% Off</span></article>
<article class="abs scard small" style="left:476px;top:2871px"><div class="name">Kestrel</div><span class="off off-row">🏷 Upto 6-7%</span></article>
<article class="abs scard small" style="left:690px;top:2871px"><div class="name">Dovara</div><span class="off off-row">🏷 Upto 6-7%</span></article>
<article class="abs scard small" style="left:904px;top:2871px"><div class="name">Kestrel</div><span class="off off-row">🏷 Upto 6-7%</span></article>
<article class="abs scard small" style="left:476px;top:3079px"><div class="name">Arclo</div><span class="off off-row">🏷 Upto 6-7%</span></article>
<article class="abs scard small" style="left:690px;top:3079px"><div class="name">Kestrel</div><span class="off off-row">🏷 Upto 6-7%</span></article>
<article class="abs scard small" style="left:904px;top:3079px"><div class="name">Fernway</div><span class="off off-row">🏷 Upto 6-7%</span></article>
<div class="abs arrow prev" style="left:558px;top:3289px"><svg width="10" height="10" viewBox="0 0 10 10"><path d="M7 1L3 5l4 4" stroke="#fff" stroke-width="2" fill="none"/></svg></div>
<div class="abs arrow next" style="left:617px;top:3289px"><svg width="10" height="10" viewBox="0 0 10 10"><path d="M3 1l4 4-4 4" stroke="#fff" stroke-width="2" fill="none"/></svg></div>

<h2 class="abs heading center" style="top:3490px">Client Testimonial</h2>
<blockquote class="abs tst" style="left:102px"><div class="stars">★★★★★</div><p>My favourite app that gave me extra discounts and cashback on brands like Shopvale, Cartnest &amp; Trendloom. Using this app for a long time and I am really enjoying its features.</p><div class="who">Ritika Joshi, Navi Mumbai</div></blockquote>
<blockquote class="abs tst" style="left:442px"><div class="stars">★★★★★</div><p>Thank You, SnoutSaver, for providing a cashback of ₹1549 on the Korvo laptop order. I must say you are truly a genuine cashback website. This review is from the heart. You rock!</p><div class="who">Arjun Mehra, Rudrapur</div></blockquote>
<blockquote class="abs tst" style="left:781px;padding-top:26px"><div class="stars">★★★★★</div><p>Lot of options variety easy to choose thank you! last week I redeemed my SnoutSaver balance to Shopvale. They gave full instructions about to redeem the amount. I redeemed my amount and feel very happy.</p><div class="who">Kavin Raman, Patna</div></blockquote>
<div class="abs arrow prev" style="left:558px;top:3840px"><svg width="10" height="10" viewBox="0 0 10 10"><path d="M7 1L3 5l4 4" stroke="#fff" stroke-width="2" fill="none"/></svg></div>
<div class="abs arrow next" style="left:617px;top:3840px"><svg width="10" height="10" viewBox="0 0 10 10"><path d="M3 1l4 4-4 4" stroke="#fff" stroke-width="2" fill="none"/></svg></div>

<section class="abs news">
  <h2>Subscribe Our<br>Newsletter</h2>
  <p>It has survived not only five centuries, but also the leap into electronic</p>
  <div class="mail">Enter Mail ID<span class="sub">Subscribe →</span></div>
</section>
<div class="abs news-photo" role="img" aria-label="Photo of a smiling woman holding a small terrier puppy"></div>

<div class="abs perk" style="left:176px"><svg width="24" height="24" viewBox="0 0 24 24" fill="none" stroke="#f15a29" stroke-width="1.6"><path d="M2 7h12v9H2zM14 10h4l3 3v3h-7z"/><circle cx="6" cy="18" r="2"/><circle cx="17" cy="18" r="2"/></svg><div><b>Free Shipping</b><small>On all orders above ₹499</small></div></div>
<div class="abs perk" style="left:411px"><svg width="24" height="24" viewBox="0 0 24 24" fill="none" stroke="#f15a29" stroke-width="1.6"><path d="M20 12a8 8 0 1 1-3-6.2"/><path d="M18 2v4h-4"/></svg><div><b>Free Returns</b><small>Within 7 days(T&amp;Cs Apply)</small></div></div>
<div class="abs perk" style="left:648px"><svg width="24" height="24" viewBox="0 0 24 24" fill="none" stroke="#f15a29" stroke-width="1.6"><circle cx="12" cy="12" r="9"/><path d="M12 7v6M12 16v1"/></svg><div><b>Best Deals</b><small>On Pet Products</small></div></div>
<div class="abs perk" style="left:882px"><svg width="24" height="24" viewBox="0 0 24 24" fill="none" stroke="#f15a29" stroke-width="1.6"><circle cx="12" cy="12" r="9"/><path d="M5 14v-3a7 7 0 0 1 14 0v3"/></svg><div><b>We Support</b><small>Monday-Saturday,9am to<br>9pm</small></div></div>

<footer class="abs footer">
  <div class="abs brand" style="left:106px;top:64px;font-size:26px"><span class="dot"></span>SnoutSaver</div>
  <p class="abs" style="left:106px;top:122px;width:250px;font-size:13px;color:#555;line-height:1.5">Lorem Ipsum has been the industry's standard</p>
  <div class="abs social" style="left:106px;top:226px"><i></i><i></i><i></i><i></i><i></i></div>
  <span class="abs vline" style="left:378px"></span>
  <span class="abs vline" style="left:628px"></span>
  <span class="abs vline" style="left:878px"></span>
  <div class="abs fcol" style="left:439px"><h6>Information</h6><a>List Your Business</a><a>Privacy Policy</a><a>Terms &amp; Conditions</a></div>
  <div class="abs fcol" style="left:697px"><h6>Categories</h6><a>Hot Deal</a><a>Popular stores</a><a>Latest deals</a></div>
  <div class="abs fcol" style="left:954px"><h6>How It Works</h6><a>FAQs</a><a>How It Works</a><a>Contact Us</a></div>
  <div class="abs copy">© 2025,&nbsp;<b style="color:var(--navy)">SNOUTSAVER</b>. All Rights Reserved.</div>
</footer>

</body>
</html>
```